Web Design for a Biotech Consulting Firm

We need a web site design for a new business based in Philadelphia called Verantel Dx. This is a consulting firm that will serve medical diagnostics industry, which is part of the life science/healthcare industry focusing on developing and marketing products that help in early detection, monitoring or management of diseases. Our consulting firm will help medical diagnostic companies to overcome key challenges in designing, evaluating and marketing new products.Our Verantel Dx is Verantel Dx. Verantel is Latin word for "something" Dx represents diagnostics. The idea behind the name is that we help companies to transform the original, early product ideas ("nothing") into "something"; which is a product with full clinical utility that will help to improve health and well-being.The web site should use the visual feel of the logo (attached), be modern, simple and clean looking and represent creativity, innovation, scientific thinking and progress.
Updates

Wix Design is acceptable

Industry/Entity Type

Biotechnology

Coding

Coded - Design and coding required

Number of Pages Required

1 page

Font styles to use
Sans Serif

Requirements
Must have
• simple, clean look couple of pages
Should not have
• a lot of pages

```html
<!DOCTYPE html>
<html lang="en">
<head>
<meta charset="utf-8">
<title>Verantel Dx</title>
<link href="https://fonts.googleapis.com/css2?family=Montserrat:wght@300;700;800&family=Lato:wght@400;700&display=swap" rel="stylesheet">
<style>
:root{
  --blue:#1f84f0;
  --blue-dark:#1670d8;
  --blue-light:#3d95f4;
  --ink:#2f2f35;
  --grey:#555a60;
  --text:#6a6d72;
  --panel:#ededee;
  --footer:#1d2028;
  --bar:#14161b;
  --white:#ffffff;
  --gold:#f5b400;
}
*{box-sizing:border-box;margin:0;padding:0}
html,body{width:1200px;height:4269px;overflow:hidden}
body{font-family:"Lato",sans-serif;background:var(--white);color:var(--ink)}
.page{position:relative;width:1200px;height:4269px;overflow:hidden}
.abs{position:absolute}
.photo{position:absolute}

/* header */
.site-header{position:absolute;left:0;top:0;width:1200px;height:111px;background:var(--blue)}
.brand{position:absolute;display:flex;align-items:center;gap:10px;font-family:"Lato",sans-serif;font-weight:400;color:var(--white)}
.brand-mark{width:14px;height:14px;border:2px solid currentColor}
.site-header .brand{left:166px;top:38px;font-size:24px}
.nav a{position:absolute;top:44px;font-family:"Lato",sans-serif;font-size:17px;color:var(--white);text-decoration:none;transform:translateX(-50%);white-space:nowrap}
.nav a.active{color:var(--gold)}

/* hero */
.hero{position:absolute;left:0;top:111px;width:1200px;height:600px}
.hero-photo{left:0;top:0;width:1200px;height:600px;background:radial-gradient(ellipse at 70% 40%,#f1f4fb 0%,#d3def4 30%,#a7bce8 60%,#7f9fdc 100%)}
.social-rail{position:absolute;left:1105px;top:0;width:95px;height:600px;background:rgba(70,80,98,.82)}
.social-rail span{position:absolute;left:39px;width:18px;height:18px;border:2px solid var(--white);border-radius:3px}
.hero-title{position:absolute;left:676px;top:170px;font-family:"Montserrat",sans-serif;font-weight:800;font-size:58px;color:#111;letter-spacing:1px}
.hero-sub{position:absolute;left:676px;top:244px;font-family:"Montserrat",sans-serif;font-weight:300;font-size:52px;color:#111}
.hero-curve{position:absolute;left:0;top:480px}

/* who */
.who-pattern{left:0;top:745px;width:240px;height:536px;background-color:var(--blue);background-image:radial-gradient(rgba(255,255,255,.18) 1px,transparent 1.5px);background-size:6px 6px}
.who-photo{left:20px;top:832px;width:439px;height:364px;background:radial-gradient(ellipse at 45% 55%,#1a2550 0%,#131c3c 45%,#6f7890 75%,#e6e9ee 100%);box-shadow:0 4px 14px rgba(0,0,0,.15)}
.section-heading{font-family:"Montserrat",sans-serif;font-weight:800;font-size:40px;letter-spacing:1px}
.who-heading{left:550px;top:795px;color:var(--ink)}
.who-heading em{font-style:normal;color:var(--blue)}
.who-text{left:550px;top:853px;width:506px;font-size:15.5px;line-height:29px;color:var(--text);text-align:justify}
.btn{position:absolute;display:flex;align-items:center;justify-content:center;background:var(--blue);color:var(--white);font-family:"Montserrat",sans-serif;font-weight:700;text-decoration:none}
.btn-read{left:550px;top:1125px;width:146px;height:50px;font-size:15px;border-radius:3px}

/* services */
.services{position:absolute;left:0;top:1326px;width:1200px;height:490px}
.services-panel{position:absolute;left:0;top:0;width:618px;height:490px;background:var(--blue)}
.services-photo{left:618px;top:0;width:582px;height:490px;background:radial-gradient(ellipse at 50% 60%,#6d6fb8 0%,#a9abd6 35%,#e4e6f1 70%,#f6f7fa 100%)}
.services-heading{left:104px;top:48px;color:var(--white)}
.service-list{position:absolute;left:0;top:0;list-style:none}
.service-list li{position:absolute;left:110px;display:flex;align-items:center;gap:20px;font-family:"Montserrat",sans-serif;font-weight:700;font-size:23px;color:var(--white);white-space:nowrap}
.service-list svg{flex:none}
.badge{position:absolute;left:576px;top:191px;width:110px;height:110px;border-radius:50%;background:var(--white);display:flex;align-items:center;justify-content:center;box-shadow:0 0 0 4px rgba(255,255,255,.35)}
.badge .brand{position:static;color:#333;font-size:15px;gap:5px}
.badge .brand-mark{width:9px;height:9px}

/* products */
.products-heading{left:0;top:1875px;width:1200px;text-align:center;color:var(--grey)}
.product{position:absolute;top:2015px;width:244px;height:285px;background:var(--white);box-shadow:0 6px 14px rgba(0,0,0,.22)}
.product .photo{left:0;top:0;width:244px;height:218px}
.product-label{position:absolute;left:0;bottom:0;width:244px;height:67px;background:var(--blue);color:var(--white);display:flex;align-items:center;justify-content:center;font-family:"Montserrat",sans-serif;font-weight:700;font-size:18px;letter-spacing:.5px}
.btn-more{left:510px;top:2353px;width:160px;height:55px;font-size:21px}

/* testimonials */
.testimonials{position:absolute;left:0;top:2489px;width:1200px;height:477px;background:var(--panel)}
.testimonials-heading{left:0;top:46px;width:1200px;text-align:center;color:var(--grey)}
.review{position:absolute;top:171px;width:306px;height:202px;background:var(--white);box-shadow:0 2px 6px rgba(0,0,0,.08)}
.avatar{position:absolute;left:6px;top:52px;width:96px;height:96px;border-radius:50%}
.review-title{position:absolute;left:110px;right:0;top:26px;text-align:center;font-weight:700;font-size:16px;color:#333}
.stars{position:absolute;left:110px;right:0;top:52px;text-align:center;color:var(--gold);font-size:17px;letter-spacing:2px}
.review-text{position:absolute;left:110px;right:0;top:80px;text-align:center;font-style:italic;font-size:14px;line-height:26px;color:#9a9ca0}
.review-name{position:absolute;left:110px;right:0;top:158px;text-align:center;font-size:16px;color:#333}
.dots{position:absolute;left:565px;top:431px;display:flex;gap:7px}
.dots span{width:18px;height:18px;border-radius:50%;background:var(--blue)}
.dots span.off{background:none;border:2px solid var(--blue)}

/* gallery */
.gallery-heading{left:0;top:3017px;width:1200px;text-align:center;color:var(--ink)}
.g{box-shadow:0 10px 20px rgba(140,200,240,.25)}
.arrow{position:absolute;top:3389px;width:50px;height:50px;border-radius:50%;background:var(--blue);display:flex;align-items:center;justify-content:center}

/* footer */
.footer{position:absolute;left:0;top:3810px;width:1200px;height:382px}
.footer-bg{position:absolute;left:0;top:0}
.footer .brand{left:568px;top:100px;font-size:18px}
.contact{position:absolute;top:188px;display:flex;align-items:center;gap:12px;font-size:15px;color:var(--white);font-weight:700;white-space:nowrap}
.footer-nav a{position:absolute;top:245px;transform:translateX(-50%);font-size:17px;color:var(--white);text-decoration:none;white-space:nowrap}
.footer-social span{position:absolute;top:312px;width:20px;height:20px;border:2px solid var(--white);border-radius:3px}
.bottom-bar{position:absolute;left:0;top:4192px;width:1200px;height:77px;background:var(--bar);color:var(--white);font-size:14px;display:flex;align-items:center;padding-left:119px}
</style>
</head>
<body>
<div class="page">

  <header class="site-header">
    <div class="brand"><span class="brand-mark"></span>Verantel Dx</div>
    <nav class="nav">
      <a href="#" class="active" style="left:393px">HOME</a>
      <a href="#" style="left:499px">SERVICES</a>
      <a href="#" style="left:646px">OUR PROJECTS</a>
      <a href="#" style="left:792px">TRAININGS</a>
      <a href="#" style="left:906px">BLOG</a>
      <a href="#" style="left:1024px">CONTACT US</a>
    </nav>
  </header>

  <section class="hero">
    <div class="photo hero-photo" role="img" aria-label="Medical scanner equipment in blue light"></div>
    <div class="social-rail" aria-label="Social links">
      <span style="top:35px"></span><span style="top:82px"></span><span style="top:129px"></span><span style="top:176px"></span><span style="top:223px"></span>
    </div>
    <h1 class="hero-title">WELCOME TO</h1>
    <p class="hero-sub">Verantel DX</p>
    <svg class="hero-curve" width="1200" height="120" viewBox="0 0 1200 120" aria-hidden="true">
      <path d="M0 120 L0 100 Q600 -20 1200 100 L1200 120 Z" fill="#fff"/>
      <path d="M40 84 Q600 -30 1200 88" fill="none" stroke="#1f84f0" stroke-width="6"/>
    </svg>
  </section>

  <div class="photo who-pattern" aria-hidden="true"></div>
  <div class="photo who-photo" role="img" aria-label="Patient vital signs monitor screen"></div>
  <h2 class="abs section-heading who-heading">WHO <em>WE ARE</em></h2>
  <p class="abs who-text">Lorem ipsum dolor sit amet, consectetur adipiscing elit, sed do eiusmod tempor incididunt ut labore et dolore magna aliqua. Quis ipsum suspendisse ultrices gravida. Risus commodo viverra maecenas accumsan lacus vel facilisis. Lorem ipsum dolor sit amet, consectetur adipiscing elit, sed do eiusmod tempor incididunt ut labore et dolore magna aliqua. Quis ipsum suspendisse ultrices gravida. Risus commodo viverra maecenas accumsan lacus vel facilisis.</p>
  <a href="#" class="btn btn-read">READ MORE</a>

  <section class="services">
    <div class="services-panel">
      <svg class="abs" style="left:0;top:0" width="618" height="490" aria-hidden="true"><path d="M0 490 L618 200 L618 490 Z" fill="#3d95f4" opacity=".55"/></svg>
    </div>
    <div class="photo services-photo" role="img" aria-label="Hands resting on a medical scanner"></div>
    <h2 class="abs section-heading services-heading">OUR SERVICES</h2>
    <ul class="service-list">
      <li style="top:131px"><svg width="30" height="30" viewBox="0 0 30 30"><g fill="#fff"><rect x="11" y="1" width="8" height="8" transform="rotate(45 15 5)"/><rect x="1" y="11" width="8" height="8" transform="rotate(45 5 15)"/><rect x="21" y="11" width="8" height="8" transform="rotate(45 25 15)"/><rect x="11" y="21" width="8" height="8" transform="rotate(45 15 25)"/></g></svg>Blood Glucose Meters</li>
      <li style="top:186px"><svg width="30" height="30" viewBox="0 0 30 30"><g fill="#fff"><rect x="11" y="1" width="8" height="8" transform="rotate(45 15 5)"/><rect x="1" y="11" width="8" height="8" transform="rotate(45 5 15)"/><rect x="21" y="11" width="8" height="8" transform="rotate(45 25 15)"/><rect x="11" y="21" width="8" height="8" transform="rotate(45 15 25)"/></g></svg>Pulse Oximeters</li>
      <li style="top:243px"><svg width="30" height="30" viewBox="0 0 30 30"><g fill="#fff"><rect x="11" y="1" width="8" height="8" transform="rotate(45 15 5)"/><rect x="1" y="11" width="8" height="8" transform="rotate(45 5 15)"/><rect x="21" y="11" width="8" height="8" transform="rotate(45 25 15)"/><rect x="11" y="21" width="8" height="8" transform="rotate(45 15 25)"/></g></svg>Gspaculum</li>
      <li style="top:308px"><svg width="30" height="30" viewBox="0 0 30 30"><g fill="#fff"><rect x="11" y="1" width="8" height="8" transform="rotate(45 15 5)"/><rect x="1" y="11" width="8" height="8" transform="rotate(45 5 15)"/><rect x="21" y="11" width="8" height="8" transform="rotate(45 25 15)"/><rect x="11" y="21" width="8" height="8" transform="rotate(45 15 25)"/></g></svg>Walkers</li>
      <li style="top:373px"><svg width="30" height="30" viewBox="0 0 30 30"><g fill="#fff"><rect x="11" y="1" width="8" height="8" transform="rotate(45 15 5)"/><rect x="1" y="11" width="8" height="8" transform="rotate(45 5 15)"/><rect x="21" y="11" width="8" height="8" transform="rotate(45 25 15)"/><rect x="11" y="21" width="8" height="8" transform="rotate(45 15 25)"/></g></svg>Humidifiers</li>
    </ul>
    <div class="badge"><div class="brand"><span class="brand-mark"></span>Verantel Dx</div></div>
  </section>

  <h2 class="abs section-heading products-heading">PRODUCTS</h2>
  <article class="product" style="left:65px"><div class="photo" role="img" aria-label="Vital sign monitor" style="background:radial-gradient(ellipse at 50% 45%,#2a3550 0%,#8b93a3 35%,#e3e5e9 60%,#ffffff 85%)"></div><div class="product-label">VITAL SIGN MONITOR</div></article>
  <article class="product" style="left:340px"><div class="photo" role="img" aria-label="Digital sphygmomanometer" style="background:radial-gradient(ellipse at 50% 50%,#5a5c60 0%,#b4b6ba 35%,#eeeff0 62%,#ffffff 85%)"></div><div class="product-label">SPYGMOMANOMETER</div></article>
  <article class="product" style="left:613px"><div class="photo" role="img" aria-label="Blood pressure gauge and bulb" style="background:radial-gradient(ellipse at 45% 50%,#1e1f22 0%,#5c5e62 30%,#dcdde0 60%,#ffffff 82%)"></div><div class="product-label">BLOOD PRESSURE</div></article>
  <article class="product" style="left:888px"><div class="photo" role="img" aria-label="Blood sugar test meter" style="background:radial-gradient(ellipse at 50% 50%,#c4ccd6 0%,#e4e8ed 35%,#f7f8fa 60%,#ffffff 85%)"></div><div class="product-label">SUGAR TEST</div></article>
  <a href="#" class="btn btn-more">View More</a>

  <section class="testimonials">
    <h2 class="abs section-heading testimonials-heading">TESTIMONIAL</h2>
    <article class="review" style="left:109px">
      <div class="avatar" role="img" aria-label="Portrait of client" style="background:radial-gradient(circle at 50% 45%,#b07a58 0%,#7a5440 50%,#e4b95c 100%)"></div>
      <div class="review-title">Harbor Lanes</div><div class="stars">★★★★★</div>
      <p class="review-text">Lorem ipsum dolor sit<br>amet, consecteturlacus</p>
      <div class="review-name">Nora Vell</div>
    </article>
    <article class="review" style="left:447px">
      <div class="avatar" role="img" aria-label="Portrait of client" style="background:radial-gradient(circle at 50% 45%,#b88670 0%,#6a463a 50%,#a9b0b4 100%)"></div>
      <div class="review-title">Quiet Tour</div><div class="stars">★★★★★</div>
      <p class="review-text">Lorem ipsum dolor sit<br>amet, consecteturlacus</p>
      <div class="review-name">Theo Marsh</div>
    </article>
    <article class="review" style="left:779px">
      <div class="avatar" role="img" aria-label="Portrait of client" style="background:radial-gradient(circle at 50% 45%,#c29a80 0%,#4e3a2e 50%,#d8d6d2 100%)"></div>
      <div class="review-title">Coastline</div><div class="stars">★★★★★</div>
      <p class="review-text">Lorem ipsum dolor sit<br>amet, consecteturlacus</p>
      <div class="review-name">Ivan Lorde</div>
    </article>
    <div class="dots"><span class="off"></span><span></span><span></span></div>
  </section>

  <h2 class="abs section-heading gallery-heading">GALLERY</h2>
  <div class="photo g" role="img" aria-label="Dental treatment chair" style="left:144px;top:3124px;width:284px;height:280px;background:radial-gradient(ellipse at 45% 60%,#5aa0dc 0%,#a9cdec 40%,#eef4f9 85%)"></div>
  <div class="photo g" role="img" aria-label="Hospital operating room" style="left:439px;top:3124px;width:308px;height:280px;background:radial-gradient(ellipse at 50% 55%,#e8f2fa 0%,#9cc6e6 45%,#5d95c6 100%)"></div>
  <div class="photo g" role="img" aria-label="Laboratory sample tubes in a rack" style="left:757px;top:3124px;width:283px;height:280px;background:radial-gradient(ellipse at 50% 50%,#1f4fa8 0%,#4f7fc6 35%,#cfdcee 75%,#eef2f7 100%)"></div>
  <div class="photo g" role="img" aria-label="Intensive care room with equipment" style="left:144px;top:3424px;width:360px;height:281px;background:radial-gradient(ellipse at 50% 60%,#3f6d96 0%,#7fa9cf 40%,#d3e4f1 90%)"></div>
  <div class="photo g" role="img" aria-label="Patient monitor displaying vital signs" style="left:525px;top:3424px;width:515px;height:281px;background:radial-gradient(ellipse at 40% 55%,#1a2550 0%,#121a38 45%,#5e677f 75%,#e4e7ec 100%)"></div>
  <div class="arrow" style="left:43px"><svg width="24" height="24" viewBox="0 0 24 24"><path d="M20 12H5M11 5l-7 7 7 7" fill="none" stroke="#fff" stroke-width="3" stroke-linecap="round" stroke-linejoin="round"/></svg></div>
  <div class="arrow" style="left:1097px"><svg width="24" height="24" viewBox="0 0 24 24"><path d="M4 12h15M13 5l7 7-7 7" fill="none" stroke="#fff" stroke-width="3" stroke-linecap="round" stroke-linejoin="round"/></svg></div>

  <footer class="footer">
    <svg class="footer-bg" width="1200" height="382" viewBox="0 0 1200 382" aria-hidden="true">
      <path d="M0 85 Q600 -40 1200 85 L1200 382 L0 382 Z" fill="#1d2028"/>
      <path d="M150 56 Q600 -20 1060 50" fill="none" stroke="#1f84f0" stroke-width="6"/>
    </svg>
    <div class="brand"><span class="brand-mark"></span>Verantel Dx</div>
    <div class="contact" style="left:242px"><svg width="20" height="20" viewBox="0 0 24 24"><path d="M12 2a7 7 0 0 0-7 7c0 5 7 13 7 13s7-8 7-13a7 7 0 0 0-7-7zm0 9.5A2.5 2.5 0 1 1 12 6.5a2.5 2.5 0 0 1 0 5z" fill="#1f84f0"/></svg>Philadelphia, PA</div>
    <div class="contact" style="left:430px"><svg width="20" height="20" viewBox="0 0 24 24"><path d="M6.6 10.8a15 15 0 0 0 6.6 6.6l2.2-2.2a1 1 0 0 1 1-.25 11.4 11.4 0 0 0 3.6.57 1 1 0 0 1 1 1V20a1 1 0 0 1-1 1A17 17 0 0 1 3 4a1 1 0 0 1 1-1h3.5a1 1 0 0 1 1 1c0 1.25.2 2.45.57 3.57a1 1 0 0 1-.25 1z" fill="#1f84f0"/></svg>(555) 214-0187</div>
    <div class="contact" style="left:654px"><svg width="24" height="18" viewBox="0 0 24 18"><rect x="0" y="0" width="24" height="18" rx="2" fill="#1f84f0"/><path d="M2 3l10 7 10-7" fill="none" stroke="#1d2028" stroke-width="2"/></svg>info@verantel-dx.com</div>
    <nav class="footer-nav">
      <a href="#" style="left:326px">Home</a>
      <a href="#" style="left:421px">Services</a>
      <a href="#" style="left:547px">Our Projects</a>
      <a href="#" style="left:669px">Trainings</a>
      <a href="#" style="left:767px">Blog</a>
      <a href="#" style="left:865px">Contact us</a>
    </nav>
    <div class="footer-social" aria-label="Social links">
      <span style="left:474px"></span><span style="left:532px"></span><span style="left:596px"></span><span style="left:659px"></span><span style="left:716px"></span>
    </div>
  </footer>

  <div class="bottom-bar">© 2019 Copyrights Verantel Dx | All Rights Reserved</div>
</div>
</body>
</html>
```